ORV Fashion Design Company Needs a New Web Design, Please Click Me

Designers:

PLEASE NOTE: we only need the web page design, not a fully coded website.

Our brand's name is Orbel Vantra, our signature is print. our style is edgy and chic.

The old website is too messy. here's the address:
www.orvdesign.example.cn

The new website's purpose is to show our brand/design and most importantly, sell products, So it should be a combination of a designer official website and online shopping. I want the whole style to be clean, edgy and pioneer, easy to understand. we need a sophisticated online shopping website.

The reference websites are:
liromapek.example.uk
www.qd-besu.example
talemkorv.example
misolvare.example
pardelunitram.example

Please beat their designs :)

Check out our lasted fashion show to get to know us more.

https://www.videohost.example/watch?v=ZkrpLmWnaYd&spfreload=10

The attachments are our Logo and some 2015 Look Book.
(Please let us know if you want to play with our print in this particular web design, we can send the source file.)
Updates

Designers, we really like the design of helenamardoux.example(we have attached a picture of the website) , Can we get a homepage like that? so the designs you submit will be 3 pages. The first one should be a page that only has Shop/Look. then the shop page, it should be nothing but our product which we will list the categories ourself. And the look page should contain all the info. such as news, about us and designers etc. Thank you all for your hard work, we really enjoyed the designs. Added Monday, November 03, 2014

Target Market(s)

Our target audiences are woman aged from 16-40 who like online shopping

Industry/Entity Type

Online Shopping

Number of Pages Required

3 page

Font styles to use
Serif
Sans Serif
Script

Requirements
Must have
• Designers,
• we really like the design of helenamardoux.example(we have attached a picture of the website) , Can we get a homepage like that? so the designs you submit will be 3 pages. The first one should be a page that only has Shop/Look. then the shop page, it should be nothing but our product which we will list the categories ourself. And the look page should contain all the info. such as news, about us and designers etc. Thank you all for your hard work, we really enjoyed the designs.

```html
<!DOCTYPE html>
<html lang="en">
<head>
<meta charset="utf-8">
<title>Orbel Vantra — Home</title>
<link href="https://fonts.googleapis.com/css2?family=Cinzel:wght@400;500&family=Mulish:wght@400&display=swap" rel="stylesheet">
<style>
  :root {
    --paper: #ffffff;
    --ink: #3a3a3a;
    --ink-soft: #555555;
    --accent: #d21f26;
    --rule: #e2e2e2;
    --night: #0f1012;
    --night-2: #16181c;
    --print-pale: #c9d6e4;
    --print-blue: #4f80b4;
    --print-mid: #2f5680;
    --print-deep: #162a42;
    --light: #f4f4f4;
  }
  * { box-sizing: border-box; margin: 0; padding: 0; }
  html, body { width: 1200px; height: 844px; overflow: hidden; }
  body {
    position: relative;
    background: var(--paper);
    font-family: "Mulish", sans-serif;
    color: var(--ink);
  }
  .sidebar {
    position: absolute; left: 0; top: 0;
    width: 291px; height: 844px;
    background: var(--paper);
  }
  .brand {
    position: absolute; left: 18px; top: 20px; width: 256px;
    text-align: center;
  }
  .brand-mark {
    width: 96px; height: 96px; margin: 0 auto;
    border-radius: 50%;
    background: var(--accent);
  }
  .brand-name {
    font-family: "Cinzel", serif;
    font-weight: 400;
    color: #111;
    line-height: 1;
    white-space: nowrap;
  }
  .brand-group { font-size: 23px; letter-spacing: 2px; margin-top: 6px; }
  .brand-title { font-size: 27px; letter-spacing: 2.4px; margin-top: 1px; }
  .main-nav {
    position: absolute; left: 20px; top: 219px; width: 252px;
    list-style: none;
  }
  .main-nav li {
    height: 43px; line-height: 43px;
    text-align: center; font-size: 15px;
    color: var(--ink-soft);
    border-bottom: 1px solid var(--rule);
  }
  .main-nav li:last-child { border-bottom: none; }
  .main-nav li.is-current { color: var(--accent); }
  .social {
    position: absolute; left: 0; width: 291px; top: 769px;
    display: flex; justify-content: center; gap: 12px;
  }
  .social span {
    width: 14px; height: 14px; border-radius: 50%;
    background: #9a9a9a;
  }
  .copyright {
    position: absolute; left: 0; width: 291px; top: 806px;
    text-align: center; font-size: 13px; color: var(--ink-soft);
  }
  .hero {
    position: absolute; left: 291px; top: 0;
    width: 909px; height: 844px;
    background: linear-gradient(90deg, var(--night-2), var(--night) 50%, var(--night-2));
    overflow: hidden;
  }
  .hero-print {
    position: absolute; left: 150px; top: 0; width: 628px; height: 844px;
    background:
      radial-gradient(ellipse 22% 40% at 50% 50%, rgba(201,214,228,0.55), transparent 75%),
      radial-gradient(ellipse 50% 12% at 50% 28%, rgba(201,214,228,0.35), transparent 80%),
      radial-gradient(ellipse 50% 12% at 50% 72%, rgba(201,214,228,0.35), transparent 80%),
      linear-gradient(90deg, var(--night-2) 0%, var(--print-deep) 12%, var(--print-mid) 30%, var(--print-blue) 50%, var(--print-mid) 70%, var(--print-deep) 88%, var(--night-2) 100%);
  }
  .hero-title {
    position: absolute; left: 0; width: 909px; top: 388px;
    text-align: center;
    font-family: "Cinzel", serif; font-weight: 500;
    font-size: 58px; letter-spacing: 0;
    line-height: 1;
    color: var(--light);
    white-space: nowrap;
  }
  .account {
    position: absolute; right: 28px; top: 24px;
    display: flex; align-items: center;
    font-size: 13.5px; color: var(--light);
  }
  .account .divider {
    width: 1px; height: 15px; background: #888; margin: 0 12px;
  }
</style>
</head>
<body>
  <aside class="sidebar">
    <div class="brand">
      <div class="brand-mark"></div>
      <div class="brand-name brand-group">ORV GROUP</div>
      <div class="brand-name brand-title">ORBEL VANTRA</div>
    </div>
    <ul class="main-nav">
      <li class="is-current">Shop</li>
      <li>Look</li>
    </ul>
    <div class="social" aria-label="Social links">
      <span></span><span></span><span></span>
    </div>
    <p class="copyright">Copyright © 2014 ORV Group.</p>
  </aside>

  <main class="hero">
    <div class="hero-print" role="img" aria-label="Mirrored brand print of fine white line work over blue smoke on black"></div>
    <h1 class="hero-title">ORBEL VANTRA</h1>
    <nav class="account">
      <span>Login</span>
      <span class="divider"></span>
      <span>Register</span>
    </nav>
  </main>
</body>
</html>
```